Homepage layout for online ad network

Attached is our Valtro Media logo and updated brief (I can't seem to delete the old logo and brief, but they're no longer relevant).

This project was originally posted with a different logo and corporate name, but we have decided to stay with our current logo and name and redesign the site.

Your design is for a homepage only - design, no coding (I'll get someone else to take your PSD and code it).

Your homepage will make use of a Flash slider - BUT YOU ARE NOT REQUIRED TO PROVIDE THE FLASH. Instead, simply provide the layout and at least two static examples out of the four different sections that will eventually be in the slider.

Much of this design is based on the design of a competitor (listed in the brief).

Please ask whatever questions you need to in order to clarify instructions.
Updates

Project updated to include new logo (and correspondingly new color scheme).

Brief changed slightly.

Thank you for submitting designs for this project in the past.

After some internal strategy work, we have decided to retain our initial corporate identity, Valtro Media.

If you have submitted a design for the original brief and are available, please re-work your best prior design to reflect the color scheme in the newly uploaded logo.

Target Market(s)

This site is aimed primarily at young professionals who buy digital media on behalf of large advertisers.

Industry/Entity Type

Media

Requirements
Must have
• modern white space
Should not have
• no Flash outside of slider

```html
<!DOCTYPE html>
<html lang="en">
<head>
<meta charset="utf-8">
<title>Valtro Media — Beauty</title>
<link rel="stylesheet" href="https://fonts.googleapis.com/css2?family=Montserrat:wght@500;700&family=Arimo:ital,wght@0,400;0,700;1,700&family=Pathway+Gothic+One&display=swap">
<style>
  :root {
    --red: #c4122f;
    --red-bright: #e8101a;
    --red-deep: #4a0508;
    --lime: #d4e02a;
    --lime-light: #f6f66c;
    --ink: #1c1c1c;
    --body: #333333;
    --panel: #f8f8f8;
    --rule: #555555;
    --pink-a: #f3c6e0;
    --pink-b: #ead3e3;
  }
  * { margin: 0; padding: 0; box-sizing: border-box; }
  html, body { width: 1200px; height: 1050px; overflow: hidden; background: #fff; }
  body { position: relative; font-family: "Arimo", Arial, sans-serif; color: var(--body); }

  .brand { position: absolute; left: 145px; top: 18px; display: flex; align-items: center; gap: 12px; }
  .brand-mark { width: 36px; height: 36px; background: var(--lime); }
  .brand-name { font-family: "Montserrat", sans-serif; font-weight: 500; font-size: 34px; color: var(--ink); letter-spacing: -0.5px; }

  .tagline { position: absolute; right: 119px; top: 11px; font-family: "Montserrat", sans-serif; font-weight: 700; font-size: 11px; color: var(--red); letter-spacing: .3px; }

  .main-nav { position: absolute; right: 118px; top: 63px; display: flex; }
  .main-nav a { font-family: "Montserrat", sans-serif; font-weight: 700; font-size: 12.5px; color: var(--ink); text-decoration: none; padding: 6px 14px; border-left: 1px solid var(--rule); line-height: 15px; }
  .main-nav a:first-child { border-left: none; }
  .main-nav a:nth-child(2) { border-left-color: var(--red); }
  .main-nav a:last-child { padding-right: 0; }

  .hero { position: absolute; left: 0; top: 101px; width: 1200px; height: 161px;
    background: linear-gradient(180deg, var(--red-bright) 0%, #d40c14 45%, #8a0a0d 80%, var(--red-deep) 100%); }
  .hero-title { position: absolute; left: 218px; top: 42px; font-family: "Montserrat", sans-serif; font-weight: 700; font-size: 40px; color: var(--lime); text-shadow: 1px 2px 3px rgba(0,0,0,.35); line-height: 46px; }
  .hero-sub { position: absolute; left: 219px; top: 88px; font-family: "Montserrat", sans-serif; font-weight: 700; font-size: 21px; line-height: 24px; color: #fff; text-shadow: 1px 2px 3px rgba(0,0,0,.4); }

  .content { position: absolute; left: 130px; top: 290px; width: 960px; height: 616px; background: var(--panel);
    box-shadow: 0 -6px 10px -6px rgba(0,0,0,.25), 0 10px 12px -8px rgba(0,0,0,.35); }
  .sidebar { position: absolute; left: 611px; top: 0; width: 349px; height: 100%; box-shadow: inset 10px 0 10px -8px rgba(0,0,0,.12); }

  .section-head { position: absolute; left: 5px; top: 28px; display: flex; align-items: center; gap: 12px; }
  .section-mark { width: 20px; height: 20px; background: var(--lime); border: 3px solid var(--red); }
  .section-title { font-family: "Pathway Gothic One", sans-serif; font-size: 28px; color: var(--ink); }

  .lead { position: absolute; left: 5px; top: 79px; width: 560px; font-size: 18px; line-height: 24px; color: var(--red); }
  .copy { position: absolute; font-size: 14px; line-height: 24px; color: var(--body); }
  .copy-intro { left: 6px; top: 136px; width: 570px; }
  .copy-side { left: 319px; top: 186px; width: 260px; }
  .copy-wide { left: 8px; top: 449px; width: 570px; }

  .pull-quote { position: absolute; left: 4px; top: 191px; width: 284px; height: 242px; padding: 12px 16px 0 20px;
    background: linear-gradient(90deg, var(--lime-light) 0%, #e4e82c 40%, var(--lime) 100%); box-shadow: 2px 3px 5px rgba(0,0,0,.35); }
  .pull-quote p { font-weight: 700; font-style: italic; font-size: 14.5px; line-height: 24px; color: var(--red); }
  .pull-quote cite { position: absolute; right: 19px; bottom: 4px; font-style: normal; font-weight: 700; font-size: 14px; color: var(--ink); }

  .footer-rule { position: absolute; left: 8px; top: 543px; width: 577px; height: 1px; background: var(--rule); }
  .footer-nav { position: absolute; left: 5px; top: 565px; display: flex; }
  .footer-nav a { font-family: "Montserrat", sans-serif; font-weight: 500; font-size: 13px; color: var(--ink); text-decoration: none; display: flex; align-items: center; gap: 5px; }
  .footer-nav a svg { width: 13px; height: 11px; }

  .partners-badge { position: absolute; left: 0; top: 29px; width: 240px; height: 38px; background: linear-gradient(90deg, var(--lime-light), var(--lime));
    box-shadow: 2px 3px 5px rgba(0,0,0,.35); font-family: "Pathway Gothic One", sans-serif; font-size: 26px; color: var(--red); padding-left: 32px; line-height: 38px; }
  .partner-name { position: absolute; left: 18px; font-size: 20px; color: var(--red); }
  .partner-shot { position: absolute; left: 26px; border: 1px solid #ddd; }
  .shot-one { top: 126px; width: 258px; height: 173px; background: linear-gradient(90deg, var(--pink-a), #fff 30%, #fff 70%, var(--pink-a)); }
  .shot-two { top: 365px; width: 259px; height: 180px; background: var(--pink-b); }

  .copyright { position: absolute; left: 0; top: 935px; width: 1210px; text-align: center; font-size: 11.5px; color: var(--ink); }
</style>
</head>
<body>
  <header>
    <div class="brand"><span class="brand-mark"></span><span class="brand-name">Valtro Media</span></div>
    <p class="tagline">COMPANY TAGLINE GOES HERE</p>
    <nav class="main-nav">
      <a href="#">BEAUTY</a><a href="#">COOKING</a><a href="#">PARENTING</a><a href="#">ENTERTAINMENT</a><a href="#">VIDEO</a><a href="#">CPC</a>
    </nav>
  </header>

  <section class="hero">
    <h1 class="hero-title">BEAUTY</h1>
    <p class="hero-sub">INSERT SECONDARY<br>MARKETING TAGLINE</p>
  </section>

  <main class="content">
    <div class="section-head"><span class="section-mark"></span><h2 class="section-title">BEAUTY</h2></div>
    <p class="lead">Lorem ipsum dolor sit amet, consectetur adipiscing elit. Mauris dignissim nulla pharetra risus iaculis at consequat turpis vulputate.</p>
    <p class="copy copy-intro">Sed scelerisque magna ut quam scelerisque dictum. Morbi purus quam, sodales id vehicula non, ultricies vitae justo. Vivamus sed augue ut elit dapibus adipiscing vel in elit.</p>

    <blockquote class="pull-quote">
      <p>“Sed scelerisque magna ut quam scelerisque dictum. Morbi purus quam, sodales id vehicula non, ultricies vitae justo. Vivamus sed augue ut elit dapibus adipiscing vel in elit. Mauris adipiscing, elit a laoreet eleifend, orci lacus condimentum enime ... ”</p>
      <cite>Owner, Company</cite>
    </blockquote>

    <p class="copy copy-side">Mauris adipiscing, elit a laoreet eleifend, orci lacus condimentum enim, vitae venenatis enim velit ac dolor. Nullam augue mauris, tincidunt et bibendum nec, consequat ut dui. Sed id ante in purus vulputate adipiscing ac non justo. Nulla libero sem, venenatis in fringilla pulvinar, ornare ac diam.<br><br>Vivamus blandit odio nec diam bibendum imperdiet. In nulla risus,</p>
    <p class="copy copy-wide">&nbsp;rhoncus ac dignissim eu, placerat quis velit. Nulla gravida, turpis et commodo congue, eros purus fermentum neque, nec viverra felis sapien ac nibh. Cras a eleifend lectus. Ut suscipit fermentum turpis, sit amet condimentum magna cursus eget.</p>

    <div class="footer-rule"></div>
    <nav class="footer-nav">
      <a href="#" style="margin-right:20px">ABOUT US <svg viewBox="0 0 13 11"><path d="M0 5.5h11M6.5 1l4.5 4.5L6.5 10" fill="none" stroke="#c4122f" stroke-width="2"/></svg></a>
      <a href="#" style="margin-right:27px">CONTACT US <svg viewBox="0 0 13 11"><path d="M0 5.5h11M6.5 1l4.5 4.5L6.5 10" fill="none" stroke="#c4122f" stroke-width="2"/></svg></a>
      <a href="#" style="margin-right:22px">MANAGEMENT TEAM <svg viewBox="0 0 13 11"><path d="M0 5.5h11M6.5 1l4.5 4.5L6.5 10" fill="none" stroke="#c4122f" stroke-width="2"/></svg></a>
      <a href="#" style="margin-right:20px">NEWS &nbsp;<svg viewBox="0 0 13 11"><path d="M0 5.5h11M6.5 1l4.5 4.5L6.5 10" fill="none" stroke="#c4122f" stroke-width="2"/></svg></a>
      <a href="#">CAREERS <svg viewBox="0 0 13 11"><path d="M0 5.5h11M6.5 1l4.5 4.5L6.5 10" fill="none" stroke="#c4122f" stroke-width="2"/></svg></a>
    </nav>

    <aside class="sidebar">
      <div class="partners-badge">VALTRO PARTNERS</div>
      <p class="partner-name" style="top:89px">31Whispers.com</p>
      <div class="partner-shot shot-one" role="img" aria-label="Screenshot of the 31Whispers.com beauty site homepage"></div>
      <p class="partner-name" style="top:329px">TheVelvetDays.com</p>
      <div class="partner-shot shot-two" role="img" aria-label="Screenshot of the TheVelvetDays.com holding page with a pink damask background"></div>
    </aside>
  </main>

  <footer class="copyright">Copyright 2011 Valtro Media. All Rights Reserved</footer>
</body>
</html>
```